Norvane Freight and Provision Service Brochure

Please see http://www.norvanefreight.example for who we are and what we do.
We would like to see a design that matches the industry we work in i.e. Oil and Gas. The design should communicate large, heavy field operations, supply of vast bulk fuel quantities to our US and Afghan Military customers, plus financial independence and the companies whatever it takes attitude operation in remote often hostile areas. Dark colors like on the website - contrasting our green logo. A strong focus on our past performance/past experience.

Target Market(s)

Military Customers, Partners, Subcontractors

Industry/Entity Type

Industry

Contact Information for Business Card

Display of Address, Phone, email etc. of our 4 offices

Font styles to use
Sans Serif

Requirements
Must have
• Glossy brochure, modern, cool design. Great display (map) of our offices in the Middle East, Europe and Central Asia. A focus on our past performance/past experience. Customer logos/references
Nice to have
• Prominent highlighted watermark logo
Should not have
• Standard A4/Letter brochure

```html
<!DOCTYPE html>
<html lang="en">
<head>
<meta charset="utf-8">
<title>Norvane Freight and Provision – What We Offer</title>
<link rel="stylesheet" href="https://fonts.googleapis.com/css2?family=PT+Sans:wght@400;700&family=Arimo:wght@400;700&display=swap">
<style>
  :root {
    --backdrop: #e7e4df;
    --panel-grey: #5b6366;
    --panel-grey-dark: #4f575a;
    --band-blue: rgba(18, 52, 92, 0.82);
    --band-blue-soft: rgba(20, 48, 84, 0.72);
    --accent-lime: #dbe51d;
    --text-light: #ffffff;
    --text-body: #f1f3f3;
  }
  * { margin: 0; padding: 0; box-sizing: border-box; }
  html, body {
    width: 1200px; height: 579px; overflow: hidden;
    background: var(--backdrop);
  }
  .spread {
    position: absolute; left: 32px; top: 52px;
    width: 1138px; height: 463px;
    background: var(--panel-grey);
    box-shadow: 0 4px 14px rgba(0,0,0,0.25);
    font-family: "Arimo", Arial, sans-serif;
    color: var(--text-body);
  }
  .page { position: absolute; top: 0; height: 463px; }
  .page--left { left: 0; width: 568px; background: var(--panel-grey); }
  .page--right { left: 568px; width: 570px; background: var(--panel-grey-dark); }

  .photo { position: absolute; }
  .photo--platform {
    left: 0; top: 0; width: 568px; height: 206px;
    background: linear-gradient(160deg, #2a78b8 0%, #1f5d96 40%, #c9a526 62%, #1a3f6a 100%);
  }
  .photo--refinery {
    left: 392px; top: 234px; width: 159px; height: 91px;
    background: linear-gradient(180deg, #7fb3dc 0%, #b7c6d3 55%, #6f7b85 100%);
  }
  .photo--map {
    left: 392px; top: 336px; width: 159px; height: 92px;
    background: linear-gradient(135deg, #c9cccc 0%, #9ea3a4 100%);
  }
  .photo--chain {
    left: 8px; top: 40px; width: 128px; height: 190px;
    background: radial-gradient(ellipse at 55% 45%, #8a5a3c 0%, #5a3826 45%, #d8d2c8 100%);
  }
  .photo--rig-dusk {
    left: 0; top: 260px; width: 570px; height: 200px;
    background: linear-gradient(180deg, #2c4f76 0%, #7a6a78 40%, #b4643a 55%, #1d3a6a 75%, #0c1f45 100%);
  }

  .offer-band {
    position: absolute; padding-left: 22px;
    font-family: "PT Sans", Arial, sans-serif;
  }
  .offer-band--fuel {
    left: 0; top: 138px; width: 568px; height: 68px; background: var(--band-blue);
  }
  .offer-band--transport {
    left: 0; top: 260px; width: 570px; height: 60px; background: var(--band-blue-soft);
    padding-left: 14px;
  }
  .offer-band__kicker {
    display: block; color: var(--text-light); font-weight: 700;
    font-size: 22px; letter-spacing: 0.2px; line-height: 1; margin-top: 12px;
  }
  .offer-band--transport .offer-band__kicker { font-size: 21px; margin-top: 9px; }
  .offer-band__title {
    display: block; color: var(--accent-lime); font-size: 18px;
    line-height: 1; margin-top: 5px; padding-left: 2px;
  }
  .offer-band--transport .offer-band__title { font-size: 19px; padding-left: 4px; margin-top: 5px; }

  .body-copy p {
    font-size: 6.4px; line-height: 8.4px; margin-bottom: 7px; text-align: justify;
  }
  .body-copy--fuel { position: absolute; left: 23px; top: 241px; width: 357px; }
  .section-heading {
    font-family: "Arimo", Arial, sans-serif; font-weight: 700;
    color: var(--accent-lime); font-size: 9.5px; margin-bottom: 5px;
  }
  .body-copy--transport { position: absolute; left: 142px; top: 46px; width: 410px; }
</style>
</head>
<body>
  <main class="spread">
    <section class="page page--left">
      <div class="photo photo--platform" role="img" aria-label="Offshore oil platform with crew in orange coveralls on deck"></div>
      <header class="offer-band offer-band--fuel">
        <span class="offer-band__kicker">WHAT WE OFFER</span>
        <span class="offer-band__title">Fuel Sourcing and Supply</span>
      </header>
      <div class="body-copy body-copy--fuel">
        <p>Norvane is the Central Asian/CEE leader in fuel supply and logistics, specializing in sourcing, supply, storage and distribution of land fuel and aviation fuel products and related services.</p>
        <p>Our core strength has been matching a widespread and highly developed fuel support network backed by robust, long standing and flexible supply arrangements with Refineries in CIS countries like Russia, Azerbaijan, Uzbekistan, Kazakhstan &amp; Turkmenistan. Our acquisition and transportation plans are elegant, robust and most importantly proven.</p>
        <p>Combined with an integrated network of modern, high capacity terminals strategically located throughout Central Asia and the CEE region, a large state of the art directly owned fleet of tanker trucks and with our key personnel along the supply chain to control processes, gain first-hand information on prevailing local conditions and react quickly and effectively to changing situations we have what it takes to provide comprehensive services and local logistical support to support every tank at all of our customers' locations throughout Central Asia and the CEE region.</p>
        <p>The result is a seamless, end-to-end, fuel procurement and management solution. Norvane is continuously finding and creating efficiencies in the supply chain to optimize our clients' overall total cost and to ensure supply reliability.</p>
      </div>
      <div class="photo photo--refinery" role="img" aria-label="Refinery towers against a blue sky"></div>
      <div class="photo photo--map" role="img" aria-label="Map of Europe, the Middle East and Central Asia with office locations marked"></div>
    </section>

    <section class="page page--right">
      <div class="photo photo--chain" role="img" aria-label="Close-up of heavy rusted chain links"></div>
      <div class="body-copy body-copy--transport">
        <h2 class="section-heading">Transportation and Logistics</h2>
        <p>Due to our large company owned trucking fleet and an extensive network of branches and partners we ensure cost effective safe and rapid transportation of cargo to our Customers in Central Asia and Europe's Central and Eastern Region. We also make sure that our customers shipments are transported via the most efficient route and reach its Central Asian and European destination safely and on time. For our customers this means: maximum flexibility as well as planning security through individually agreed upon transit times and flexible departures. Additional services such as the transportation of temperature sensitive goods and heavy cargo as well as customs clearance and 24/7 cargo tracking facilities round off Norvane service spectrum.</p>
        <p>With our fleet of more than 1400 trucks as well as long-term partnerships with preferred subcontractors we provide our customers for more than a decade with maximum capacity and flexibility for all their logistics needs. We have provided ground transport solutions that ensure safe, rapid and efficient delivery of supplies to facilities in the world's most remote and challenging environments. Over the years, our ground transport fleet has supplied US and UK Military forces, allied coalition missions, intergovernmental relief agencies, and commercial sector clients throughout Central Asia and Europe as well as the Middle East.</p>
      </div>
      <div class="photo photo--rig-dusk" role="img" aria-label="Offshore rigs on the open sea at dusk with breaking waves"></div>
      <header class="offer-band offer-band--transport">
        <span class="offer-band__kicker">WHAT WE OFFER</span>
        <span class="offer-band__title">Transportation and Logistics</span>
      </header>
    </section>
  </main>
</body>
</html>
```